Meal Plan Website Needs New Pages Designed

Brightwick Supper Kits is an online, membership based program that delivers weekly meal programs (7 days worth of recipes plus shopping lists) carefully crafted by an expert team of meal planners. All recipes are created to comply with the following macronutrient ratio: 65% healthy fats, 25% lean protein, 10% good carbs.
All recipes are Paleo friendly and a great resource for those individuals who want to correctly implement this type of diet.

We are re-designing our website and need the following pages designed:

· Home page w/ logo
· How it works page
· Get Started! page
· Recipes Page template (these will be the pages on our site that will have recipes)
· Kitchen Essentials Training page (this will be a page with videos and tips + tricks, PDFs, etc)

So 5 total PSDs, 1 for each page.

Target audience: Men and women between the ages of 30 and 60 who want to:
· Eat healthy
· Lose weight
· Follow/Implement the Paleo diet
· Take the guesswork out of preparing delicious AND healthy meals for them and their families
· Know exactly what to eat, what to buy, how to make it

Feelings/Messages we want to communicate through the design:
· “Organic” but elegant look
· Fresh/light/Airy
· Simple but NOT GENERIC
· “I want to get cooking” feeling

Our Stylistic preferences:
· Minimalist with a few bold elements (something in between)
· Easy to visually navigate (enough white space, but not too much)
· There is more to “see” than to “read”

Our Color Preferences:
· Lighter pallet
· Colors that evoke natural woods, granite countertops…
· Stay away from using all dark colors

Our Font Type Preferences:
· Easy to read
· Not more than 3 font types
· Not too rigid
· Not too sophisticated
· Simple with a touch

Examples of Website Designs that we like:
· http://www.dorvanta.com/meal-plans/
· http://grulvix.com/
· https://www.mistobarn.com/

```html
<!DOCTYPE html>
<html lang="en">
<head>
<meta charset="utf-8">
<title>Brightwick Supper Kits</title>
<link href="https://fonts.googleapis.com/css2?family=Roboto+Condensed:wght@400;700&family=Open+Sans:ital,wght@0,400;0,600;1,400&display=swap" rel="stylesheet">
<style>
:root{
  --red:#de5840;
  --brand:#b3262b;
  --text:#3a3330;
  --white:#fff;
  --charcoal:#444343;
  --night:#121212;
  --night-soft:#1e1e1e;
  --wood-1:#f0dcbb;
  --wood-2:#e8cfa8;
  --head:"Roboto Condensed", Arial, sans-serif;
  --body:"Open Sans", Arial, sans-serif;
}
*{box-sizing:border-box;margin:0;padding:0}
html,body{width:1200px;height:2560px;overflow:hidden}
body{position:relative;font-family:var(--body);color:var(--text);background:var(--white)}
.abs{position:absolute}

/* header */
.site-header{position:absolute;left:0;top:0;width:1200px;height:77px;background:var(--white);box-shadow:0 2px 4px rgba(0,0,0,.08);z-index:3}
.brand{position:absolute;left:171px;top:14px;display:flex;align-items:center;gap:10px}
.brand-square{width:50px;height:50px;background:var(--brand);border-radius:6px}
.brand-name{font-family:var(--head);font-weight:700;font-size:23px;color:var(--brand);white-space:nowrap}
.main-nav a{position:absolute;top:32px;font-family:var(--head);font-size:13px;color:#444;text-decoration:none;text-transform:uppercase;white-space:nowrap}

/* hero */
.hero{position:absolute;left:0;top:77px;width:1200px;height:428px;
  background:radial-gradient(ellipse at 55% 45%,#c9a47a 0%,#9d7a56 35%,#5b4331 70%,#2e2420 100%)}
.hero-caption{position:absolute;left:111px;top:350px;width:683px;height:44px;background:rgba(15,15,15,.88);color:var(--white);font-family:var(--head);font-size:17px;line-height:44px;padding-left:22px;text-transform:uppercase;white-space:nowrap}
.hero-arrow{position:absolute;top:350px;width:40px;height:44px;background:var(--red)}
.btn-order{position:absolute;left:111px;top:405px;width:133px;height:44px;background:var(--red);color:var(--white);font-family:var(--head);font-size:18px;line-height:44px;text-align:center;text-transform:uppercase}
.side-tab{position:absolute;left:1157px;width:43px;background:var(--red);color:var(--white);font-family:var(--head);font-size:16px;writing-mode:vertical-rl;transform:rotate(180deg);display:flex;align-items:center;justify-content:center;text-transform:uppercase;z-index:4}

/* intro band */
.intro{position:absolute;left:0;top:505px;width:1200px;height:248px;background:var(--red);color:var(--white);text-align:center}
.intro h1{font-family:var(--head);font-weight:700;font-size:29px;margin-top:45px;text-transform:uppercase}
.intro svg{display:block;margin:10px auto 0}
.intro p{width:688px;margin:22px auto 0;font-size:12.5px;line-height:22px}

/* light sections */
.light-band{position:absolute;left:0;width:1200px;background:linear-gradient(180deg,var(--wood-1),var(--wood-2))}
.section-title{position:absolute;left:0;width:1200px;text-align:center;font-family:var(--head);font-size:31px;color:var(--red);text-transform:uppercase}
.feature{position:absolute;top:877px;width:244px;height:292px;color:var(--white);text-align:center}
.feature.is-active{background:var(--red)}
.feature.is-plain{background:var(--charcoal)}
.feature-icon{width:100px;height:100px;border-radius:50%;background:var(--white);margin:39px auto 0;display:flex;align-items:center;justify-content:center}
.feature h3{font-family:var(--head);font-size:21px;font-weight:400;margin-top:20px;text-transform:uppercase}
.feature p{font-size:11px;line-height:20px;margin:12px 30px 0}

/* testimonials */
.testimonials{position:absolute;left:0;top:1227px;width:1200px;height:296px;background:linear-gradient(180deg,var(--night-soft),var(--night))}
.portrait{position:absolute;left:171px;top:1274px;width:204px;height:204px;border-radius:50%;border:8px solid var(--white);
  background:radial-gradient(circle at 45% 40%,#e2c3a3 0%,#b8936f 40%,#6e6a66 100%)}
.testimonials-title{position:absolute;left:432px;top:1274px;font-family:var(--head);font-weight:400;font-size:31px;color:var(--white);text-transform:uppercase}
.t-arrow{position:absolute;top:1283px;width:17px;height:18px;background:var(--red)}
.quote-mark{position:absolute;font-family:Georgia,serif;font-size:34px;color:#999;line-height:1}
.quote{position:absolute;left:456px;top:1352px;width:560px;font-style:italic;font-size:10.5px;line-height:20px;color:var(--white)}
.quote-name{position:absolute;left:456px;top:1428px;font-style:italic;font-size:10.5px;color:var(--red)}
.quote-role{position:absolute;left:456px;top:1448px;font-size:10.5px;color:var(--white)}

/* plans grid */
.plan{position:absolute;width:258px}
.plan h3{font-family:var(--head);font-weight:400;font-size:22px;color:var(--red);text-transform:uppercase;height:32px}
.plan-photo{width:258px;height:193px;position:relative}
.plan-photo.is-hover{background:linear-gradient(135deg,#e46a52,#d5543d)}
.read-more{position:absolute;left:44px;top:68px;width:170px;border-top:1px solid rgba(255,255,255,.8);border-bottom:1px solid rgba(255,255,255,.8);color:var(--white);text-align:center;font-family:var(--head);font-size:19px;line-height:54px;text-transform:uppercase}
.plan p{font-size:10.5px;line-height:20px;margin-top:14px;color:var(--text)}

/* footer */
.site-footer{position:absolute;left:0;top:2318px;width:1200px;height:200px;background:#0d0d0d}
.foot-link{position:absolute;width:125px;font-size:10px;color:var(--white);border-bottom:1px solid #555;padding-bottom:7px}
.foot-title{position:absolute;font-family:var(--head);font-size:13px;color:var(--red);text-transform:uppercase;white-space:nowrap}
.foot-text{position:absolute;font-size:10px;line-height:17px;color:#ccc}
.field{position:absolute;left:831px;width:195px;height:21px;border:1px solid #333;background:#111;font-size:9px;color:#888;padding:4px 8px}
.legal{position:absolute;left:0;top:2518px;width:1200px;height:42px;background:#050505}
.legal p{position:absolute;left:174px;top:14px;font-size:9px;color:#777}
.social-dot{position:absolute;top:16px;width:10px;height:10px;border-radius:50%;background:#777}
</style>
</head>
<body>

<header class="site-header">
  <div class="brand"><span class="brand-square"></span><span class="brand-name">Brightwick Supper Kits</span></div>
  <nav class="main-nav">
    <a style="left:471px">Meal Plans</a>
    <a style="left:606px">About</a>
    <a style="left:710px">How it works</a>
    <a style="left:857px">Resources</a>
    <a style="left:988px">Blog</a>
  </nav>
</header>

<section class="hero" role="img" aria-label="Close-up photograph of whole-wheat wraps filled with chicken, tomato and lettuce"></section>
<div class="hero-caption">We provide membership based program that delivers weekly meal programs</div>
<div class="hero-arrow" style="left:807px"><svg width="40" height="44"><path d="M23 15 L16 22 L23 29" stroke="#fff" stroke-width="2.5" fill="none"/></svg></div>
<div class="hero-arrow" style="left:851px"><svg width="40" height="44"><path d="M17 15 L24 22 L17 29" stroke="#fff" stroke-width="2.5" fill="none"/></svg></div>
<div class="btn-order">Order Now</div>
<div class="side-tab" style="top:116px;height:77px">Login</div>
<div class="side-tab" style="top:201px;height:120px">Register</div>

<section class="intro">
  <h1>Brightwick Supper Kits</h1>
  <svg width="180" height="16" viewBox="0 0 180 16"><line x1="0" y1="8" x2="180" y2="8" stroke="#fff" stroke-width="1"/><rect x="82" y="2" width="16" height="12" fill="var(--red)"/><circle cx="90" cy="8" r="4" fill="none" stroke="#fff" stroke-width="1.5"/></svg>
  <p>We provide membership based program that delivers weekly meal programs (7 days worth of recipes plus shopping lists) carefully crafted by an expert team of meal planners. All recipes are created to comply with the following macronutrient ratio: 65% healthy fats, 25% lean protein, 10% good carbs</p>
</section>

<section class="light-band" style="top:753px;height:474px"></section>
<h2 class="section-title" style="top:804px">Everything you need to eat healthier</h2>

<article class="feature is-active" style="left:196px">
  <div class="feature-icon"><svg width="44" height="50" viewBox="0 0 44 50"><rect x="4" y="5" width="36" height="42" rx="3" fill="none" stroke="var(--red)" stroke-width="3"/><rect x="14" y="1" width="16" height="8" rx="2" fill="var(--red)"/><path d="M10 20l3 3 5-5M10 31l3 3 5-5" stroke="var(--red)" stroke-width="2.5" fill="none"/><line x1="22" y1="21" x2="34" y2="21" stroke="var(--red)" stroke-width="3"/><line x1="22" y1="32" x2="34" y2="32" stroke="var(--red)" stroke-width="3"/></svg></div>
  <h3>Meal Plans</h3>
  <p>uncover many web sites still in their infancy. Various versions have evolved over the years...</p>
</article>
<article class="feature is-plain" style="left:480px">
  <div class="feature-icon"><svg width="60" height="50" viewBox="0 0 60 50"><circle cx="30" cy="25" r="16" fill="none" stroke="#333" stroke-width="3"/><circle cx="30" cy="25" r="10" fill="#333"/><path d="M6 6v14M3 6v10q0 5 3 5t3-5V6M6 21v24" stroke="#333" stroke-width="2.5" fill="none"/><path d="M54 6q-5 4-5 14h5v25" stroke="#333" stroke-width="3" fill="none"/></svg></div>
  <h3>Quickstart Guide</h3>
  <p>uncover many web sites still in their infancy. Various versions have evolved over the years...</p>
</article>
<article class="feature is-plain" style="left:763px">
  <div class="feature-icon"><svg width="60" height="46" viewBox="0 0 60 46"><path d="M2 14h6l6 20h18l5-14H12" stroke="#333" stroke-width="3" fill="none"/><circle cx="16" cy="40" r="3" fill="#333"/><circle cx="30" cy="40" r="3" fill="#333"/><path d="M32 18L46 4l14 14h-4v16H36V18z" fill="#333"/><rect x="43" y="24" width="6" height="10" fill="#fff"/></svg></div>
  <h3>At-Home Workouts</h3>
  <p>uncover many web sites still in their infancy. Various versions have evolved over the years...</p>
</article>

<section class="testimonials"></section>
<div class="portrait" role="img" aria-label="Portrait photograph of a smiling customer"></div>
<h2 class="testimonials-title">Testimonials</h2>
<div class="t-arrow" style="left:976px"><svg width="17" height="18"><path d="M10 5L6 9l4 4" stroke="#fff" stroke-width="1.5" fill="none"/></svg></div>
<div class="t-arrow" style="left:995px"><svg width="17" height="18"><path d="M7 5l4 4-4 4" stroke="#fff" stroke-width="1.5" fill="none"/></svg></div>
<span class="quote-mark" style="left:433px;top:1340px">&ldquo;</span>
<p class="quote">It is a long established fact that a reader will be distracted by the readable content of a page when looking at its layout. The point of using Lorem Ipsum is that it has a more-or-less normal distribution of letters, as opposed to using 'Content here, content here', making it look like readable English.</p>
<span class="quote-mark" style="left:972px;top:1412px">&rdquo;</span>
<p class="quote-name">- Lena Marwood -</p>
<p class="quote-role">Event marketer</p>

<section class="light-band" style="top:1523px;height:795px"></section>

<article class="plan" style="left:171px;top:1575px">
  <h3>Classic</h3>
  <div class="plan-photo is-hover" role="img" aria-label="Classic meal plan dish under a red overlay"><span class="read-more">Read More</span></div>
  <p>It is a long established fact that a reader will be distracted by the readable content of a page when looking at its layout. The point of using Lorem Ipsum is that it has a more-or-less normal distribution...</p>
</article>
<article class="plan" style="left:471px;top:1575px">
  <h3>For One</h3>
  <div class="plan-photo" role="img" aria-label="Bowl of fresh salad with grilled vegetables" style="background:radial-gradient(circle at 50% 50%,#c8553a,#7c9a3a 55%,#d9d6cc 100%)"></div>
  <p>It is a long established fact that a reader will be distracted by the readable content of a page when looking at its layout. The point of using Lorem Ipsum is that it has a more-or-less normal distribution...</p>
</article>
<article class="plan" style="left:772px;top:1575px">
  <h3>Lunch</h3>
  <div class="plan-photo" role="img" aria-label="Plate of tacos with lime and salsa" style="background:radial-gradient(circle at 50% 60%,#e2b54a,#9a5a2a 50%,#3a2b22 100%)"></div>
  <p>It is a long established fact that a reader will be distracted by the readable content of a page when looking at its layout. The point of using Lorem Ipsum is that it has a more-or-less normal distribution...</p>
</article>
<article class="plan" style="left:171px;top:1943px">
  <h3>Kosher</h3>
  <div class="plan-photo" role="img" aria-label="Grilled salmon fillet with green salad" style="background:radial-gradient(circle at 40% 60%,#e07a4e,#9bb25a 50%,#f2efe8 100%)"></div>
  <p>It is a long established fact that a reader will be distracted by the readable content of a page when looking at its layout. The point of using Lorem Ipsum is that it has a more-or-less normal distribution...</p>
</article>
<article class="plan" style="left:471px;top:1943px">
  <h3>Dairy Free</h3>
  <div class="plan-photo" role="img" aria-label="Savory pie with potatoes and green beans" style="background:radial-gradient(circle at 50% 45%,#e8b640,#a86a24 50%,#3e2716 100%)"></div>
  <p>It is a long established fact that a reader will be distracted by the readable content of a page when looking at its layout. The point of using Lorem Ipsum is that it has a more-or-less normal distribution...</p>
</article>
<article class="plan" style="left:772px;top:1943px">
  <h3>Gluten Free</h3>
  <div class="plan-photo" role="img" aria-label="Table of shared dishes seen from above" style="background:linear-gradient(135deg,#6b3a20,#b0703e 50%,#3a2a26 100%)"></div>
  <p>It is a long established fact that a reader will be distracted by the readable content of a page when looking at its layout. The point of using Lorem Ipsum is that it has a more-or-less normal distribution...</p>
</article>

<footer class="site-footer">
  <span class="foot-link" style="left:183px;top:45px">Meal Plans</span>
  <span class="foot-link" style="left:183px;top:75px">About</span>
  <span class="foot-link" style="left:183px;top:104px">How It Works</span>
  <span class="foot-link" style="left:183px;top:135px">Resources</span>
  <span class="foot-link" style="left:183px;top:164px;border:none">Blog</span>
  <span class="foot-link" style="left:379px;top:45px">Testimonials</span>
  <span class="foot-link" style="left:379px;top:75px">Homes Blog</span>
  <span class="foot-link" style="left:379px;top:104px">Resources</span>
  <span class="foot-link" style="left:379px;top:135px;border:none">Contact</span>
  <span class="foot-title" style="left:575px;top:45px">Latest News</span>
  <svg class="abs" style="left:758px;top:45px" width="26" height="12"><path d="M6 2L2 6l4 4M20 2l4 4-4 4" stroke="#fff" stroke-width="1.5" fill="none"/></svg>
  <p class="foot-text" style="left:575px;top:68px;width:200px">Many desktop publishing packages and web page editors now use Lorem Ipsum as their default model text...</p>
  <p class="foot-text" style="left:575px;top:134px;font-style:italic;color:var(--red)">Posted on 25 Dec 2014</p>
  <span class="foot-title" style="left:831px;top:45px">Newsletter Signup</span>
  <div class="field" style="top:67px">Name :</div>
  <div class="field" style="top:93px">Email :</div>
  <span class="foot-title" style="left:951px;top:132px;font-size:12px">Subscribe &gt;&gt;</span>
</footer>
<div class="legal">
  <p>&copy; 2014. Brightwick Supper Kits. All rights reserved.</p>
  <span class="social-dot" style="left:810px"></span>
  <span class="social-dot" style="left:838px"></span>
  <span class="social-dot" style="left:866px"></span>
  <span class="social-dot" style="left:894px"></span>
  <span class="social-dot" style="left:922px"></span>
  <span class="social-dot" style="left:950px"></span>
  <span class="social-dot" style="left:978px"></span>
</div>

</body>
</html>
```